Web Design Project for Communications Agency

The design I need (PSD file) is for an agency offering specialised PR and communications services for customers in the healthcare sector.

OBJECTIVES OF THE WEBSITE:
1. To promote the agency's communication services
2. To position Solène Brivard as an industry leader, an expert in healthcare PR and communications by highlighting blogposts and social media.

WHAT I NEED:
1st, I need the design for the Home Page ONLY.
Once approved, I will need the other pages designed as well. (Here is prototype that we've already developed for the Website that will guide you in the design:
http://qorvelle.net/solenebrivard/)

VISUAL INSPIRATION
We want to give this Website a "Flat Design" look. Here are some websites for inspiration :
- http://tavrolinkworks.com/#!/process
- http://www.brindlemoss.co/
- http://quellaroft.com/

Also, reuse images found on the company's current Website :
http://www.solenebrivard.com/fr/index.html

HOMEPAGE MAIN ELEMENTS:
1. Main menu : 6 sections
Accueil | Agence | Services | Approche | Publications | Contact

2. Main Call To Action (big dark rectangle in prototype):
Can be slider or just an information bloc.

3. Publications récentes :
The 4 latest blog posts must be features on the homepage (will be linked with the "Publications" section)

4. Dynamic Footer :
Contains a Twitter feed and a Subscribe to our Newsletter feature (revecez nos publications)

OTHER PAGES (to design once Homepage is approved)
- Agence (about us)
- Services (our team)
- Approche (our approach)
- Publications (blog articles)
- Contact (Contact us)

Industry/Entity Type

Communications

Requirements
Must have
• Please refer to prototype :
http://qorvelle.net/solenebrivard/
Must have ALL features present in prototype.

Also, must reuse this picture in the design : http://solenebrivard.com/static/images/home-big-box.jpg

Finally, you will find attached the company logo.

```html
<!DOCTYPE html>
<html lang="fr">
<head>
<meta charset="utf-8">
<title>Solène Brivard – Communications et affaires publiques</title>
<link href="https://fonts.googleapis.com/css2?family=Cabin:wght@400;500&family=Roboto+Condensed:wght@400;700&family=Roboto:wght@300;400;700&display=swap" rel="stylesheet">
<style>
  :root {
    --header-bg: #2d3033;
    --accent: #d64045;
    --accent-bright: #e04a4a;
    --section-bg: #3a3e42;
    --footer-bg: #2f3133;
    --bottom-bg: #28292b;
    --nav-text: #c9cbcd;
    --muted: #8d9094;
    --light: #d7d9db;
    --white: #ffffff;
    --field-bg: #25272a;
    --rule: #3d4043;
  }
  * { box-sizing: border-box; margin: 0; padding: 0; }
  html, body { width: 890px; height: 1200px; overflow: hidden; }
  body { position: relative; background: var(--footer-bg); font-family: "Roboto", sans-serif; }
  .abs { position: absolute; }

  .site-header { position: absolute; left: 0; top: 0; width: 890px; height: 64px; background: var(--header-bg); }
  .brand { position: absolute; left: 89px; top: 20px; display: flex; align-items: center; gap: 7px;
           font-family: "Cabin", sans-serif; font-size: 19px; color: var(--accent-bright); }
  .brand-mark { width: 10px; height: 10px; background: var(--accent-bright); }
  .main-nav a { position: absolute; top: 26px; font-family: "Cabin", sans-serif; font-size: 11px;
                color: var(--nav-text); text-decoration: none; }
  .main-nav a.current { color: var(--accent-bright); }

  .hero { position: absolute; left: 0; top: 64px; width: 890px; height: 297px; background: var(--accent); }
  .hero-title { position: absolute; left: 0; top: 74px; width: 890px; text-align: center;
                font-family: "Cabin", sans-serif; font-weight: 400; font-size: 29px; line-height: 44px; color: var(--white); }
  .hero-cta { position: absolute; left: 373px; top: 178px; width: 145px; height: 34px; background: #f4f4f4;
              font-family: "Roboto", sans-serif; font-size: 16px; color: #333; display: flex; align-items: center; justify-content: center; gap: 4px; }

  .publications { position: absolute; left: 0; top: 361px; width: 890px; height: 567px; background: var(--section-bg); }
  .section-title { position: absolute; left: 89px; top: 14px; font-family: "Cabin", sans-serif; font-weight: 400; font-size: 19px; color: var(--white); }
  .tile { position: absolute; width: 225px; height: 226px; }
  .tile-featured { background: linear-gradient(135deg, #4a5054, #3d4448 60%, #4d5a5e); }
  .tile-overlay { position: absolute; left: 22px; top: 28px; width: 190px; color: var(--white); }
  .tile-overlay h3 { font-family: "Roboto Condensed", sans-serif; font-weight: 400; font-size: 18px; }
  .tile-date { font-size: 10px; margin-top: 9px; }
  .tile-overlay p { font-size: 9px; line-height: 12.5px; margin-top: 12px; }
  .tile-btn { position: absolute; left: 23px; top: 168px; width: 86px; height: 26px; background: #f4f4f4; color: #333;
              font-size: 9px; display: flex; align-items: center; justify-content: center; gap: 3px; }

  .footer-col h4 { position: absolute; top: 957px; font-family: "Cabin", sans-serif; font-weight: 500; font-size: 11.5px; color: var(--white); }
  .tweet { position: absolute; left: 91px; width: 178px; font-size: 9.5px; line-height: 15.6px; font-weight: 300; color: var(--muted); }
  .tweet span { color: var(--accent-bright); }
  .post-link { position: absolute; left: 278px; width: 152px; height: 26px; border-bottom: 1px solid var(--rule);
               font-size: 9.5px; font-weight: 300; color: var(--light); padding-top: 1px; }
  .about { position: absolute; left: 457px; width: 170px; font-size: 9.5px; line-height: 15.6px; font-weight: 300; color: var(--light); }
  .social { position: absolute; top: 1090px; width: 16px; height: 16px; background: #55595d; }
  .field-label { position: absolute; left: 640px; font-size: 9.5px; font-weight: 300; color: var(--light); }
  .field { position: absolute; left: 640px; width: 162px; height: 26px; background: var(--field-bg); border: 1px solid #3b3e41; border-radius: 2px; }
  .subscribe { position: absolute; left: 640px; top: 1085px; width: 90px; height: 26px; background: var(--accent-bright);
               border-radius: 2px; color: var(--white); font-family: "Cabin", sans-serif; font-weight: 500; font-size: 11.5px;
               display: flex; align-items: center; justify-content: center; }

  .bottom-bar { position: absolute; left: 0; top: 1165px; width: 890px; height: 35px; background: var(--bottom-bg); }
  .copyright { position: absolute; left: 90px; top: 12px; font-size: 9.5px; font-weight: 300; color: var(--muted); }
  .legal a { position: absolute; top: 12px; font-size: 9.5px; font-weight: 300; color: var(--muted); text-decoration: none; }
</style>
</head>
<body>

<header class="site-header">
  <div class="brand"><span class="brand-mark"></span>Solène Brivard</div>
  <nav class="main-nav">
    <a class="current" style="left:367px">Home</a>
    <a style="left:422px">Accueil</a>
    <a style="left:482px">Agence</a>
    <a style="left:544px">Services</a>
    <a style="left:610px">Approche</a>
    <a style="left:681px">Publications</a>
    <a style="left:763px">Contact</a>
  </nav>
</header>

<section class="hero">
  <h1 class="hero-title">Cabinet-conseil en communications et affaires publiques<br>spécialisé dans le secteur de la santé.</h1>
  <div class="hero-cta">En Savoir Plus
    <svg width="11" height="11" viewBox="0 0 10 10"><path d="M1 1l4 4-4 4M5 1l4 4-4 4" fill="none" stroke="#333" stroke-width="1.2"/></svg>
  </div>
</section>

<section class="publications">
  <h2 class="section-title">Publication récentes</h2>

  <article class="tile tile-featured" style="left:89px;top:54px" role="img" aria-label="Photo d'un médecin en consultation, assombrie">
    <div class="tile-overlay">
      <h3>Titre de la publication</h3>
      <div class="tile-date">23 July 2013</div>
      <p>Lorem ipsum dolor sit amet, consectetur adipisicing elit, sed do eiusmod tempor incididunt ut labore et dolore magna aliqua.</p>
      <p>Ut enim ad minim veniam, quis nostrud exercitation ullamco laboris.</p>
    </div>
    <div class="tile-btn">Article Complet
      <svg width="7" height="7" viewBox="0 0 10 10"><path d="M1 1l4 4-4 4M5 1l4 4-4 4" fill="none" stroke="#333" stroke-width="1.3"/></svg>
    </div>
  </article>

  <div class="tile" style="left:333px;top:54px;background:linear-gradient(135deg,#c9c6c2,#b4b9c0 55%,#7f98b4)" role="img" aria-label="Photo d'une pédiatre examinant un jeune enfant avec un stéthoscope"></div>
  <div class="tile" style="left:576px;top:54px;background:linear-gradient(135deg,#c6c6c8,#a9a9ac 60%,#b7b7b9)" role="img" aria-label="Illustration d'un cube blanc surmonté d'une croix rouge"></div>
  <div class="tile" style="left:89px;top:305px;background:linear-gradient(135deg,#9c8a78,#7e97ab 55%,#8ea7bb)" role="img" aria-label="Photo d'une équipe de soignants en tenue de travail"></div>
  <div class="tile" style="left:333px;top:305px;background:linear-gradient(135deg,#2f5a9c,#6d92c6 55%,#2c4f8c)" role="img" aria-label="Photo d'un tensiomètre et d'un stéthoscope sur un électrocardiogramme"></div>
  <div class="tile" style="left:576px;top:305px;background:linear-gradient(135deg,#b9c3cf,#8fb0d4 50%,#d7d8da)" role="img" aria-label="Photo d'un groupe de professionnels de la santé souriants"></div>
</section>

<footer>
  <div class="footer-col">
    <h4 style="left:90px">Twitter</h4>
    <p class="tweet" style="top:980px">Velit esse cillum dolore eu fugiat nulla pariatur. Excepteur sint occaecat cupidatat non proident.<br><span>@SoleneBrivard #EnjeuSanté</span></p>
    <p class="tweet" style="top:1058px">Velit esse cillum dolore eu fugiat nulla pariatur. Excepteur sint occaecat cupidatat non proident.<br><span>@SoleneBrivard #EnjeuSanté</span></p>
  </div>

  <div class="footer-col">
    <h4 style="left:278px">Recent Post</h4>
    <div class="post-link" style="top:979px">Consectetur adipisicing elit, sed do</div>
    <div class="post-link" style="top:1005px">Consectetur adipisicing elit, sed do</div>
    <div class="post-link" style="top:1031px">Consectetur adipisicing elit, sed do</div>
    <div class="post-link" style="top:1057px">Consectetur adipisicing elit, sed do</div>
  </div>

  <div class="footer-col">
    <h4 style="left:456px">About Us</h4>
    <p class="about" style="top:980px">Consectetur adipisicing elit, sed do Eiusmod tempor incididunt ut labore.</p>
    <p class="about" style="top:1027px">Address: Street 1234, ipsum 123, dolor<br>Telephone: 0-800-123-4567<br>Fax: 0-800-123-4567</p>
    <span class="social" style="left:457px"></span>
    <span class="social" style="left:476px"></span>
    <span class="social" style="left:495px"></span>
    <span class="social" style="left:514px"></span>
    <span class="social" style="left:533px"></span>
    <span class="social" style="left:552px"></span>
  </div>

  <div class="footer-col">
    <h4 style="left:640px">Recevez nos publications</h4>
    <label class="field-label" style="top:979px">Votre nom</label>
    <div class="field" style="top:997px"></div>
    <label class="field-label" style="top:1031px">Votre courriel</label>
    <div class="field" style="top:1049px"></div>
    <div class="subscribe">Abonnez-Vous</div>
  </div>

  <div class="bottom-bar">
    <p class="copyright">© Copyrights 2013 All rights Reserved</p>
    <nav class="legal">
      <a style="left:619px">Site Map</a>
      <a style="left:672px">Terms of use</a>
      <a style="left:743px">Privacy policy</a>
    </nav>
  </div>
</footer>

</body>
</html>
```